New Company Business Card design

Looking for a corporate looking business card utilising my new logo design - the logo i would like embossed as one option and flat as another - simplistic but stylish - less is more - we are an import export business launching into the market - i would like a couple of options as main background - Grey or Black

```html
<!DOCTYPE html>
<html lang="en">
<head>
<meta charset="utf-8">
<title>Meridian Trade Group – Business Card</title>
<link rel="stylesheet" href="https://fonts.googleapis.com/css2?family=Cinzel:wght@400;600&family=Arimo:wght@400;700&display=swap">
<style>
  :root {
    --backdrop: #8a4f26;
    --grey-light: #cfd1d3;
    --grey-mid: #b3b6b9;
    --grey-dark: #9a9ea2;
    --black-light: #242526;
    --black-dark: #0b0b0c;
    --ink: #111214;
    --ink-on-black: #c9ccd0;
    --shadow: rgba(20, 8, 0, 0.55);
  }
  * { margin: 0; padding: 0; box-sizing: border-box; }
  html, body {
    width: 1200px;
    height: 900px;
    overflow: hidden;
    background: var(--backdrop);
  }
  .canvas {
    position: relative;
    width: 1200px;
    height: 900px;
  }
  .card {
    position: absolute;
    left: 330px;
    width: 556px;
    height: 343px;
    box-shadow: 3px 4px 6px var(--shadow);
    text-align: center;
  }
  .card--back {
    top: 90px;
    background: linear-gradient(160deg, var(--grey-light) 0%, var(--grey-mid) 50%, var(--grey-dark) 100%);
    color: var(--ink);
  }
  .card--front {
    top: 470px;
    width: 558px;
    background: linear-gradient(160deg, var(--black-light) 0%, var(--black-dark) 100%);
    color: var(--ink-on-black);
  }

  .holder-name {
    margin-top: 64px;
    font-family: "Cinzel", serif;
    font-weight: 600;
    font-size: 23px;
    letter-spacing: 0.5px;
    line-height: 1;
  }
  .holder-role {
    font-family: "Arimo", Arial, sans-serif;
    font-size: 15px;
    line-height: 17px;
    margin-top: 2px;
  }
  .rule {
    width: 195px;
    height: 1px;
    background: var(--ink);
    margin: 0 auto;
  }
  .rule--top { margin-top: 9px; }
  .rule--bottom { margin-top: 10px; }
  .contact-list {
    list-style: none;
    font-family: "Arimo", Arial, sans-serif;
    font-size: 15px;
    line-height: 20px;
    margin-top: 11px;
  }
  .contact-list b { font-weight: 700; }
  .address {
    font-family: "Arimo", Arial, sans-serif;
    font-size: 15px;
    line-height: 20px;
    margin-top: 16px;
  }

  .brand {
    position: absolute;
    left: 0;
    right: 0;
    top: 78px;
  }
  .brand-mark {
    display: block;
    margin: 0 auto 40px;
  }
  .brand-name {
    font-family: "Cinzel", serif;
    font-weight: 600;
    font-size: 25px;
    letter-spacing: 1px;
    line-height: 1;
  }
  .brand-rule {
    width: 356px;
    height: 1.5px;
    background: var(--ink-on-black);
    margin: 9px auto 6px;
  }
  .brand-tagline {
    font-family: "Cinzel", serif;
    font-weight: 400;
    font-size: 11px;
    letter-spacing: 2.4px;
  }
</style>
</head>
<body>
  <main class="canvas">
    <section class="card card--back" aria-label="Business card, contact side, grey stock">
      <h1 class="holder-name">DANIEL HARTLEY</h1>
      <p class="holder-role">Managing Director</p>
      <div class="rule rule--top"></div>
      <ul class="contact-list">
        <li><b>P:</b> 020-555 018 204</li>
        <li><b>M:</b> 020-555 018 205</li>
        <li><b>E:</b> hello@meridiantrade.co</li>
        <li><b>W:</b> www.meridiantrade.co</li>
      </ul>
      <div class="rule rule--bottom"></div>
      <p class="address">48 Harbour Lane, Dock Street<br>Portland, 97201.</p>
    </section>

    <section class="card card--front" aria-label="Business card, brand side, black stock">
      <div class="brand">
        <svg class="brand-mark" width="96" height="96" viewBox="0 0 96 96" aria-hidden="true">
          <circle cx="48" cy="48" r="46" fill="var(--ink-on-black)"/>
        </svg>
        <p class="brand-name">MERIDIAN TRADE GROUP</p>
        <div class="brand-rule"></div>
        <p class="brand-tagline">WORLDWIDE SUPPLY FOR LOCAL MARKETS</p>
      </div>
    </section>
  </main>
</body>
</html>
```